we can communicate on this, but i want to follow the approach we took on Pellew|Marsh & Quinlan but i feel the card front needs the black background and the platinum and gold logo. The back? I am open. we can use the same info from PM&Q. Velmont Arc is an enhanced equity investment fund - basically a very exclusive boutique hedge fund that uses only stock options. very advanced things. hope you are interested

Contact Information for Business Card

Dr. Lewis T. Brennick, CFA
Scientifique de fusée financière
701.555.0143
LTBquant47@mailvantor.com

4718 Willow Creek Bend W.
West Fargo, ND 58078

No web site

Colors

Designer to choose colors to be used in the design.

Requirements
Nice to have
• I tend to prefer the most visible applications of the logo to include logo and name, the logo version with a black background and the gold and platinum components separated by the black. I see this working well for a single side (logo and name - this is card front to me).
• I am fairly open to other treatments on the reverse side with the data. To me, it makes sense to have a different color rendition of the logo on the reverse and it may be a muted black tone on tone or an oversized portion that would have spot UV. Or, the reverse may play with colors and layout
Should not have
• Other colors = no no
• Decorative font

```html
<!DOCTYPE html>
<html lang="en">
<head>
<meta charset="utf-8">
<title>Velmont Arc – Business Card</title>
<link rel="stylesheet" href="https://fonts.googleapis.com/css2?family=Montserrat:wght@700&family=Roboto+Condensed:wght@700&family=Roboto:wght@400&display=swap">
<style>
  :root {
    --backdrop: #3b3b3d;
    --card: #1f1f21;
    --gold: #d6a72a;
    --gold-light: #f0cf5a;
    --white: #f4f4f4;
  }
  * { margin: 0; padding: 0; box-sizing: border-box; }
  html, body { width: 799px; height: 1200px; overflow: hidden; }
  body { background: var(--backdrop); position: relative; font-family: "Roboto", sans-serif; }

  .card {
    position: absolute;
    left: 80px;
    width: 640px;
    height: 366px;
    background: var(--card);
    border-radius: 4px;
    box-shadow: 0 14px 30px rgba(0,0,0,.45);
  }
  .card--front { top: 103px; }
  .card--back { top: 697px; }

  /* Brand lockup */
  .brand { position: absolute; display: flex; flex-direction: column; align-items: center; }
  .brand__dot { border-radius: 50%; background: var(--gold); }
  .brand__name {
    font-family: "Montserrat", sans-serif;
    font-weight: 700;
    color: var(--white);
    letter-spacing: .04em;
    white-space: nowrap;
    text-transform: uppercase;
    line-height: 1;
  }
  .card--front .brand { left: 0; right: 0; top: 88px; }
  .card--front .brand__dot { width: 118px; height: 118px; margin-bottom: 22px; }
  .card--front .brand__name { font-size: 52px; }

  .card--back .brand { right: 42px; top: 40px; }
  .card--back .brand__dot { width: 62px; height: 62px; margin-bottom: 12px; }
  .card--back .brand__name { font-size: 28px; }

  /* Person block */
  .person { position: absolute; left: 40px; top: 90px; }
  .person__name {
    font-family: "Roboto Condensed", sans-serif;
    font-weight: 700;
    font-size: 24px;
    color: var(--gold);
    line-height: 1.1;
    white-space: nowrap;
  }
  .person__role { font-size: 14px; color: var(--white); margin-top: 4px; }

  .divider {
    position: absolute;
    left: 40px; right: 40px; top: 168px;
    height: 2px;
    background: linear-gradient(90deg, var(--gold) 0%, var(--gold-light) 45%, rgba(214,167,42,.35) 100%);
  }

  .contact { position: absolute; left: 40px; top: 186px; list-style: none; }
  .contact__item { display: flex; align-items: center; gap: 10px; font-size: 15px; color: var(--white); height: 26px; white-space: nowrap; }
  .contact__icon { width: 14px; height: 14px; flex: none; }

  .address {
    position: absolute; right: 42px; bottom: 40px;
    text-align: right; font-size: 16px; line-height: 1.45; color: var(--white);
    font-style: normal; white-space: nowrap;
  }
</style>
</head>
<body>

  <section class="card card--front" aria-label="Card front">
    <div class="brand">
      <div class="brand__dot"></div>
      <p class="brand__name">Velmont Arc</p>
    </div>
  </section>

  <section class="card card--back" aria-label="Card back">
    <div class="person">
      <h1 class="person__name">Dr. Lewis T. Brennick, CFA</h1>
      <p class="person__role">Scientifique de fusée financière</p>
    </div>

    <div class="brand">
      <div class="brand__dot"></div>
      <p class="brand__name">Velmont Arc</p>
    </div>

    <div class="divider"></div>

    <ul class="contact">
      <li class="contact__item">
        <svg class="contact__icon" viewBox="0 0 24 24" aria-hidden="true">
          <path fill="#d6a72a" d="M6.6 10.8a15.1 15.1 0 0 0 6.6 6.6l2.2-2.2a1 1 0 0 1 1-.25 11.4 11.4 0 0 0 3.6.57 1 1 0 0 1 1 1V20a1 1 0 0 1-1 1A17 17 0 0 1 3 4a1 1 0 0 1 1-1h3.5a1 1 0 0 1 1 1c0 1.25.2 2.45.57 3.57a1 1 0 0 1-.25 1z"/>
        </svg>
        701.555.0143
      </li>
      <li class="contact__item">
        <svg class="contact__icon" viewBox="0 0 24 24" aria-hidden="true">
          <rect x="2" y="5" width="20" height="14" rx="1" fill="#d6a72a"/>
          <path d="M2.5 5.5 12 13l9.5-7.5" fill="none" stroke="#1f1f21" stroke-width="1.8"/>
        </svg>
        LTBquant47@mailvantor.com
      </li>
    </ul>

    <address class="address">
      4718 Willow Creek Bend W.<br>
      West Fargo, ND 58078
    </address>
  </section>

</body>
</html>
```